Maple Roster Business Card for recruitment company

We are looking for a Business Card Design that incorporates our personal details and our busines name and logo. We are a specialized search consultancy that recruit Property and Construction professionals.
We would like a business card that stands out and is appealing to the Construction and Property industry as well.

Target Market(s)

people in the construction and property industry

Contact Information for Business Card

Business Name and logo

Font styles to use
Serif

Colors
0094D4
00A9DD
6FCCEA
C7EBF8
E9F6FB

Requirements
Must have
• Business name and logo as well as contact details
Should not have
• No photos of us please

```html
<!DOCTYPE html>
<html lang="en">
<head>
<meta charset="utf-8">
<title>Maple Roster — Business Card</title>
<link rel="stylesheet" href="https://fonts.googleapis.com/css2?family=Open+Sans:wght@300;400;700&display=swap">
<style>
  :root {
    --backdrop: #1d2126;
    --card: #033d52;
    --ink: #ffffff;
    --rule: #9aa7ad;
  }
  * { box-sizing: border-box; margin: 0; padding: 0; }
  html, body {
    width: 1200px; height: 780px; overflow: hidden;
    background: var(--backdrop);
    font-family: "Open Sans", Arial, sans-serif;
    color: var(--ink);
  }
  .stage {
    width: 1200px; height: 780px;
    display: flex; align-items: center; justify-content: center; gap: 44px;
  }
  .card {
    width: 520px; height: 298px;
    background: var(--card);
    border-radius: 16px;
    position: relative;
  }
  .brand {
    font-weight: 300;
    text-transform: uppercase;
    letter-spacing: 0.08em;
    color: var(--ink);
    white-space: nowrap;
  }
  .card--front { display: flex; align-items: center; justify-content: center; }
  .card--front .brand { font-size: 46px; }

  .card--back .brand {
    position: absolute; left: 38px; top: 62px;
    font-size: 27px;
  }
  .divider {
    position: absolute; left: 262px; top: 112px;
    width: 1px; height: 150px; background: var(--rule);
  }
  .person { position: absolute; left: 290px; top: 40px; }
  .person__name { font-weight: 700; font-size: 22px; letter-spacing: 0.04em; line-height: 1.1; }
  .person__title { font-weight: 400; font-size: 11px; letter-spacing: 0.06em; margin-top: 2px; }
  .contacts { position: absolute; left: 290px; top: 126px; list-style: none; }
  .contacts li {
    display: flex; align-items: flex-start; gap: 9px;
    font-size: 12.5px; letter-spacing: 0.05em; line-height: 1.35;
    margin-bottom: 12px;
  }
  .contacts svg { width: 13px; height: 13px; flex: none; margin-top: 2px; }
</style>
</head>
<body>
  <main class="stage">
    <section class="card card--front" aria-label="Card front">
      <span class="brand">Maple Roster</span>
    </section>

    <section class="card card--back" aria-label="Card back">
      <span class="brand">Maple Roster</span>
      <div class="divider"></div>
      <div class="person">
        <p class="person__name">Karim Haddad</p>
        <p class="person__title">General Manager</p>
      </div>
      <ul class="contacts">
        <li>
          <svg viewBox="0 0 16 16" fill="none" stroke="#fff" stroke-width="1.2"><path d="M4 1.5l2.2 3-1.4 1.6a9 9 0 0 0 5.1 5.1l1.6-1.4 3 2.2-1.4 2.3C8 14 2 8 1.7 2.9z"/></svg>
          <span>041-552-7384</span>
        </li>
        <li>
          <svg viewBox="0 0 16 16" fill="none" stroke="#fff" stroke-width="1.2"><rect x="1.5" y="3.5" width="13" height="9"/><path d="M1.5 3.5l6.5 5 6.5-5"/></svg>
          <span>hello@mapleroster.com</span>
        </li>
        <li>
          <svg viewBox="0 0 16 16" fill="none" stroke="#fff" stroke-width="1.2"><circle cx="8" cy="8" r="6.5"/><ellipse cx="8" cy="8" rx="3" ry="6.5"/><path d="M1.5 8h13M2.5 4.8h11M2.5 11.2h11"/></svg>
          <span>www.mapleroster.com</span>
        </li>
        <li>
          <svg viewBox="0 0 16 16" fill="none" stroke="#fff" stroke-width="1.2"><path d="M8 10.5S4.5 7 4.5 4.8a3.5 3.5 0 0 1 7 0C11.5 7 8 10.5 8 10.5z"/><circle cx="8" cy="4.8" r="1.2"/><ellipse cx="8" cy="12.8" rx="5" ry="1.6"/></svg>
          <span>482 Cedar Hollow Road<br>Brookfield, VA 20140</span>
        </li>
      </ul>
    </section>
  </main>
</body>
</html>
```